Velvet Circle club

We are looking to redesign the user interface of our mobile app “Velvet Circle”, which is the official rewards program for our luxury casino brand, Kestrane Harbour.
Our goal is to give the app a more elegant, premium, and user-friendly design that reflects the exclusivity of our brand and the luxury experience we offer our VIP clientele.
What We Need:
A complete UI design for the app’s main screens, including:
Splash Screen
01 Login / Signup Screen
02 Home Dashboard
Buttons -
Home / my card / my wallet / my booking / my host
My wallet / my offer / lucky game / my taxi / entertainment / online
03 Profile screen
04 My wallet
05 My offer
06Packages
07 My booking
08 My host
09 My card
we attached our privies app all the screen for you reference
Inspiration:
Think of luxury brands like Dunmore-Vale, Corvix Onyx, or high-end lifestyle apps. Clean interfaces, classy animations, and a sense of exclusivity are key.
We’re excited to see fresh, innovative takes that elevate the app to a truly world-class luxury experience for our users.
Thank you!
Casino

```html
<!DOCTYPE html>
<html lang="en">
<head>
<meta charset="utf-8">
<title>Velvet Circle – App Screens</title>
<link href="https://fonts.googleapis.com/css2?family=Inter:wght@400;500;600;700&display=swap" rel="stylesheet">
<style>
:root{
  --canvas:#c9c9c9;
  --screen:#1c1d22;
  --card:#23252b;
  --line:#33353d;
  --orange:#f0a93a;
  --red:#e5262e;
  --text:#ffffff;
  --muted:#9a9ca3;
}
*{box-sizing:border-box;margin:0;padding:0}
html,body{width:1200px;height:588px;overflow:hidden}
body{background:var(--canvas);font-family:"Inter",sans-serif;color:var(--text);position:relative}
.phone{position:absolute;top:54px;width:375px;height:812px;background:var(--screen);transform-origin:top left;transform:scale(.537);overflow:hidden}
.phone.tall{height:895px}
.abs{position:absolute}
.status{position:absolute;top:16px;left:22px;right:18px;display:flex;justify-content:space-between;align-items:center;font-size:15px;font-weight:600}
.status svg{display:block}
.brand{display:flex;align-items:center;gap:8px;color:var(--orange);font-weight:600}
.brand .dot{width:14px;height:14px;border-radius:50%;background:var(--red)}
/* login */
.title{font-size:32px;font-weight:700;line-height:42px}
.sub{font-size:12px;color:#c9cad0}
.label{font-size:12px;color:#c9cad0}
.field{position:absolute;left:24px;width:327px;height:46px;border:1px solid var(--line);border-radius:8px;background:#1f2026;display:flex;align-items:center;padding:0 14px;font-size:14px;justify-content:space-between}
.btn{position:absolute;background:var(--orange);border-radius:6px;display:flex;align-items:center;justify-content:center;color:#fff;font-size:14px;font-weight:500}
.circle-btn{position:absolute;width:40px;height:40px;border-radius:50%;background:#2b2d34;display:flex;align-items:center;justify-content:center}
/* home */
.hero{position:absolute;left:0;top:125px;width:375px;height:205px;background:radial-gradient(circle at 55% 55%,#8a6a2c 0%,#3b2c17 40%,#15130f 80%)}
.tile{position:absolute;width:162px;height:120px;background:var(--card);border:1px solid var(--line);border-radius:14px;display:flex;flex-direction:column;align-items:center;justify-content:center;gap:12px;font-size:14px}
.tabbar{position:absolute;left:0;bottom:0;width:375px;height:87px;background:var(--card);border-radius:18px 18px 0 0}
.tab{position:absolute;top:20px;display:flex;flex-direction:column;align-items:center;gap:6px;font-size:11px;color:#6d6f77}
.tab.active{color:var(--orange)}
.fab{position:absolute;left:162px;top:-30px;width:52px;height:52px;background:var(--red);border-radius:12px;transform:rotate(45deg);display:flex;align-items:center;justify-content:center}
.fab svg{transform:rotate(-45deg)}
/* offers */
.offer{position:absolute;left:16px;width:342px;height:142px;background:var(--card);border:1px solid var(--line);border-radius:14px;overflow:hidden}
.offer .mark{position:absolute;left:20px;top:-6px;width:62px;height:62px;border-radius:50%;background:#15161a}
.offer .name{position:absolute;left:96px;top:20px;font-size:16px;font-weight:600}
.offer .pct{position:absolute;left:20px;top:83px;width:40px;height:40px;border:1px solid var(--orange);border-radius:6px;color:var(--orange);font-size:15px;font-weight:600;display:flex;align-items:center;justify-content:center}
.offer .note{position:absolute;left:69px;top:84px;font-size:12px;color:var(--muted);line-height:18px}
.offer .redeem{left:225px;top:83px;width:98px;height:40px;font-size:14px}
/* spin */
.center-text{position:absolute;left:0;width:375px;text-align:center}
.spin-title{font-size:28px;font-weight:600}
.spin-sub{font-size:14px;color:#d4d5da}
.dim{opacity:.25}
.modal{position:absolute;left:57px;top:245px;width:261px;height:323px;border-radius:12px;background:radial-gradient(circle at 50% 45%,#5a2a12 0%,#2a1710 55%,#141012 100%)}
.close{position:absolute;left:296px;top:240px;width:28px;height:28px;border-radius:50%;background:#2b2d34;display:flex;align-items:center;justify-content:center}
</style>
</head>
<body>

<!-- Login -->
<section class="phone" style="left:54px">
  <div class="status"><span>9:41</span>
    <svg width="76" height="14" viewBox="0 0 76 14"><rect x="0" y="9" width="3" height="4" fill="#fff"/><rect x="5" y="6" width="3" height="7" fill="#fff"/><rect x="10" y="3" width="3" height="10" fill="#fff"/><rect x="15" y="0" width="3" height="13" fill="#fff"/><path d="M28 5a10 10 0 0 1 14 0l-2 2a7 7 0 0 0-10 0zM31 8a5 5 0 0 1 8 0l-4 4z" fill="#fff"/><rect x="50" y="1" width="22" height="11" rx="3" fill="none" stroke="#fff"/><rect x="52" y="3" width="16" height="7" rx="1" fill="#fff"/></svg>
  </div>
  <div class="brand abs" style="left:24px;top:175px;font-size:22px"><span class="dot"></span>Velvet Circle</div>
  <h1 class="title abs" style="left:24px;top:248px">Sign in to your<br>Account</h1>
  <p class="sub abs" style="left:24px;top:345px">Enter your email and password to log in</p>
  <p class="label abs" style="left:24px;top:414px">Email</p>
  <div class="field" style="top:433px">mara.quell@example.com</div>
  <p class="label abs" style="left:24px;top:499px">Password</p>
  <div class="field" style="top:518px">*******
    <svg width="16" height="16" viewBox="0 0 16 16" fill="none" stroke="#9a9ca3" stroke-width="1.3"><path d="M1 8s2.5-4.5 7-4.5S15 8 15 8s-2.5 4.5-7 4.5S1 8 1 8z"/><circle cx="8" cy="8" r="2"/><path d="M2 2l12 12"/></svg>
  </div>
  <p class="abs" style="right:24px;top:582px;font-size:12px;color:var(--orange)">Forgot Password ?</p>
  <div class="btn" style="left:24px;top:622px;width:327px;height:48px">Log In</div>
</section>

<!-- Home -->
<section class="phone tall" style="left:277px">
  <div class="status"><span>9:41</span>
    <svg width="76" height="14" viewBox="0 0 76 14"><rect x="0" y="9" width="3" height="4" fill="#fff"/><rect x="5" y="6" width="3" height="7" fill="#fff"/><rect x="10" y="3" width="3" height="10" fill="#fff"/><rect x="15" y="0" width="3" height="13" fill="#fff"/><path d="M28 5a10 10 0 0 1 14 0l-2 2a7 7 0 0 0-10 0zM31 8a5 5 0 0 1 8 0l-4 4z" fill="#fff"/><rect x="50" y="1" width="22" height="11" rx="3" fill="none" stroke="#fff"/><rect x="52" y="3" width="16" height="7" rx="1" fill="#fff"/></svg>
  </div>
  <div class="circle-btn" style="left:16px;top:64px"><svg width="16" height="12"><path d="M1 1h14M1 6h14M1 11h14" stroke="#fff" stroke-width="1.4"/></svg></div>
  <div class="brand abs" style="left:128px;top:76px;font-size:15px"><span class="dot" style="width:10px;height:10px"></span>Velvet Circle</div>
  <div class="abs" style="left:255px;top:72px;height:26px;width:50px;border-radius:13px;background:#2b2d34;display:flex;align-items:center;gap:4px;padding-left:7px;font-size:11px"><span style="width:12px;height:12px;border-radius:50%;background:var(--orange)"></span>270</div>
  <div class="circle-btn" style="left:313px;top:64px"><svg width="16" height="18" fill="none" stroke="#fff" stroke-width="1.4"><path d="M3 13V8a5 5 0 0 1 10 0v5l1.5 2h-13zM6.5 16.5a1.5 1.5 0 0 0 3 0"/><circle cx="12.5" cy="3" r="2.3" fill="#f0a93a" stroke="none"/></svg></div>
  <div class="hero" role="img" aria-label="Casino scene with roulette wheel, slot reels, dice, cards and gold coins"></div>

  <div class="tile" style="left:16px;top:350px">
    <svg width="50" height="44" viewBox="0 0 50 44"><path d="M8 10l26-8 3 8z" fill="#f0a93a"/><rect x="2" y="10" width="46" height="32" rx="3" fill="#f0a93a"/><rect x="30" y="20" width="18" height="12" rx="2" fill="#23252b"/><circle cx="37" cy="26" r="2.5" fill="#f0a93a"/></svg>My Wallet</div>
  <div class="tile" style="left:196px;top:350px">
    <svg width="48" height="48" viewBox="0 0 48 48"><path d="M24 2l6 5 8-1 2 8 7 4-3 7 3 7-7 4-2 8-8-1-6 5-6-5-8 1-2-8-7-4 3-7-3-7 7-4 2-8 8 1z" fill="#f0a93a"/><path d="M16 32l16-16" stroke="#23252b" stroke-width="3"/><circle cx="17" cy="17" r="3.5" fill="#23252b"/><circle cx="31" cy="31" r="3.5" fill="#23252b"/></svg>My Offer</div>
  <div class="tile" style="left:16px;top:489px">
    <svg width="44" height="46" viewBox="0 0 44 46" fill="none" stroke="#f0a93a" stroke-width="2"><circle cx="22" cy="20" r="15"/><circle cx="22" cy="20" r="9"/><path d="M22 5v30M7 20h30M11 9l22 22M33 9L11 31"/><path d="M12 38h20v5H12z" fill="#f0a93a"/></svg>Lucky Game</div>
  <div class="tile" style="left:196px;top:489px">
    <svg width="52" height="46" viewBox="0 0 52 46"><rect x="18" y="0" width="16" height="7" fill="#f0a93a"/><path d="M10 10h32l6 14H4z" fill="#f0a93a"/><rect x="2" y="22" width="48" height="16" rx="3" fill="#f0a93a"/><rect x="6" y="36" width="8" height="9" fill="#f0a93a"/><rect x="38" y="36" width="8" height="9" fill="#f0a93a"/><path d="M14 13h24l3 9H11z" fill="#23252b"/><circle cx="10" cy="29" r="3" fill="#23252b"/><circle cx="42" cy="29" r="3" fill="#23252b"/></svg>My Taxi</div>
  <div class="tile" style="left:16px;top:628px">
    <svg width="50" height="48" viewBox="0 0 50 48" fill="none" stroke="#f0a93a" stroke-width="2"><circle cx="14" cy="14" r="11"/><path d="M14 3v22M3 14h22"/><path d="M2 46V32l10-6 10 6v14M28 46V30h18v16M34 20l4-8 4 8"/><circle cx="43" cy="6" r="4" fill="#f0a93a"/></svg>Entertainment</div>
  <div class="tile" style="left:196px;top:628px">
    <svg width="48" height="46" viewBox="0 0 48 46" fill="none" stroke="#f0a93a" stroke-width="2.2"><rect x="3" y="6" width="42" height="30" rx="2"/><circle cx="24" cy="17" r="5"/><path d="M15 31a9 9 0 0 1 18 0M16 44h16M24 36v8"/><rect x="19" y="1" width="10" height="6" fill="#f0a93a"/></svg>Online</div>

  <nav class="tabbar">
    <div class="fab"><svg width="24" height="20" fill="none" stroke="#fff" stroke-width="2"><rect x="1" y="3" width="22" height="16" rx="2"/><path d="M1 8h22M15 13h4"/></svg></div>
    <div class="tab active" style="left:16px"><svg width="24" height="24" fill="none" stroke="#f0a93a" stroke-width="1.6"><path d="M3 11l9-8 9 8v10h-6v-6H9v6H3z"/></svg>Home</div>
    <div class="tab" style="left:84px"><svg width="26" height="24" fill="none" stroke="#6d6f77" stroke-width="1.6"><rect x="1" y="4" width="24" height="16" rx="2"/><path d="M1 9h24M17 15h4"/></svg>My Card</div>
    <div class="tab" style="left:226px"><svg width="24" height="24" fill="none" stroke="#6d6f77" stroke-width="1.6"><rect x="2" y="4" width="20" height="18" rx="2"/><path d="M2 10h20M7 2v4M17 2v4"/></svg>My Booking</div>
    <div class="tab" style="left:316px"><svg width="24" height="24" fill="none" stroke="#6d6f77" stroke-width="1.6"><rect x="4" y="2" width="16" height="20" rx="2"/><path d="M8 8h8M8 12h8M8 16h5"/></svg>My Host</div>
  </nav>
</section>

<!-- My Offer -->
<section class="phone tall" style="left:499px">
  <div class="status"><span>9:41</span>
    <svg width="76" height="14" viewBox="0 0 76 14"><rect x="0" y="9" width="3" height="4" fill="#fff"/><rect x="5" y="6" width="3" height="7" fill="#fff"/><rect x="10" y="3" width="3" height="10" fill="#fff"/><rect x="15" y="0" width="3" height="13" fill="#fff"/><path d="M28 5a10 10 0 0 1 14 0l-2 2a7 7 0 0 0-10 0zM31 8a5 5 0 0 1 8 0l-4 4z" fill="#fff"/><rect x="50" y="1" width="22" height="11" rx="3" fill="none" stroke="#fff"/><rect x="52" y="3" width="16" height="7" rx="1" fill="#fff"/></svg>
  </div>
  <svg class="abs" style="left:18px;top:70px" width="20" height="16" fill="none" stroke="#fff" stroke-width="1.6"><path d="M19 8H2M8 2L2 8l6 6"/></svg>
  <div class="center-text" style="top:68px;font-size:16px;font-weight:500">My Offer</div>
  <div class="circle-btn" style="left:319px;top:58px"><svg width="16" height="18" fill="none" stroke="#fff" stroke-width="1.4"><path d="M3 13V8a5 5 0 0 1 10 0v5l1.5 2h-13zM6.5 16.5a1.5 1.5 0 0 0 3 0"/><circle cx="12.5" cy="3" r="2.3" fill="#f0a93a" stroke="none"/></svg></div>

  <article class="offer" style="top:127px"><span class="mark"></span><h3 class="name">Aurelle Spa</h3><span class="pct">25%</span><p class="note">Only to Kestrane Harbour<br>Members</p><span class="btn redeem">Redeem</span></article>
  <article class="offer" style="top:288px"><span class="mark"></span><h3 class="name">Nine Lantern Spa</h3><span class="pct">25%</span><p class="note">Only to Kestrane Harbour<br>Members</p><span class="btn redeem">Redeem</span></article>
  <article class="offer" style="top:449px"><span class="mark"></span><h3 class="name">Solace Spa</h3><span class="pct">25%</span><p class="note">Only to Kestrane Harbour<br>Members</p><span class="btn redeem">Redeem</span></article>
  <article class="offer" style="top:610px"><span class="mark"></span><h3 class="name">Tidewell Spa</h3><span class="pct">25%</span><p class="note">Only to Kestrane Harbour<br>Members</p><span class="btn redeem">Redeem</span></article>

  <nav class="tabbar">
    <div class="fab"><svg width="24" height="20" fill="none" stroke="#fff" stroke-width="2"><rect x="1" y="3" width="22" height="16" rx="2"/><path d="M1 8h22M15 13h4"/></svg></div>
    <div class="tab active" style="left:16px"><svg width="24" height="24" fill="none" stroke="#f0a93a" stroke-width="1.6"><path d="M3 11l9-8 9 8v10h-6v-6H9v6H3z"/></svg>Home</div>
    <div class="tab" style="left:84px"><svg width="26" height="24" fill="none" stroke="#6d6f77" stroke-width="1.6"><rect x="1" y="4" width="24" height="16" rx="2"/><path d="M1 9h24M17 15h4"/></svg>My Card</div>
    <div class="tab" style="left:226px"><svg width="24" height="24" fill="none" stroke="#6d6f77" stroke-width="1.6"><rect x="2" y="4" width="20" height="18" rx="2"/><path d="M2 10h20M7 2v4M17 2v4"/></svg>My Booking</div>
    <div class="tab" style="left:316px"><svg width="24" height="24" fill="none" stroke="#6d6f77" stroke-width="1.6"><rect x="4" y="2" width="16" height="20" rx="2"/><path d="M8 8h8M8 12h8M8 16h5"/></svg>My Host</div>
  </nav>
</section>

<!-- Spin the Wheel -->
<section class="phone" style="left:722px">
  <div class="status"><span>9:41</span>
    <svg width="76" height="14" viewBox="0 0 76 14"><rect x="0" y="9" width="3" height="4" fill="#fff"/><rect x="5" y="6" width="3" height="7" fill="#fff"/><rect x="10" y="3" width="3" height="10" fill="#fff"/><rect x="15" y="0" width="3" height="13" fill="#fff"/><path d="M28 5a10 10 0 0 1 14 0l-2 2a7 7 0 0 0-10 0zM31 8a5 5 0 0 1 8 0l-4 4z" fill="#fff"/><rect x="50" y="1" width="22" height="11" rx="3" fill="none" stroke="#fff"/><rect x="52" y="3" width="16" height="7" rx="1" fill="#fff"/></svg>
  </div>
  <svg class="abs" style="left:18px;top:62px" width="20" height="16" fill="none" stroke="#fff" stroke-width="1.6"><path d="M19 8H2M8 2L2 8l6 6"/></svg>
  <div class="abs" role="img" aria-label="Game title lettering" style="left:125px;top:125px;width:125px;height:40px;border-radius:8px;background:linear-gradient(90deg,#c41e1e,#f0a93a,#c41e1e)"></div>
  <h2 class="center-text spin-title" style="top:192px">Spin the Wheel</h2>
  <p class="center-text spin-sub" style="top:235px">5 more spins ready in 23:09:07</p>
  <svg class="abs" style="left:17px;top:307px" width="340" height="340" viewBox="0 0 340 340">
    <defs><linearGradient id="ring" x1="0" y1="0" x2="1" y2="1"><stop offset="0" stop-color="#f0a93a"/><stop offset=".35" stop-color="#e23a8c"/><stop offset=".7" stop-color="#35c6e8"/><stop offset="1" stop-color="#f5d23a"/></linearGradient></defs>
    <circle cx="170" cy="170" r="166" fill="#121316" stroke="url(#ring)" stroke-width="3"/>
    <circle cx="170" cy="170" r="145" fill="none" stroke="url(#ring)" stroke-width="2"/>
    <path d="M170 170L115.3 37.9A143 143 0 0 1 224.7 37.9Z" fill="#f7931e"/>
    <path d="M170 170L224.7 37.9A143 143 0 0 1 302.1 115.3Z" fill="#f8ab1c"/>
    <path d="M170 170L302.1 115.3A143 143 0 0 1 302.1 224.7Z" fill="#1fb9ec"/>
    <path d="M170 170L302.1 224.7A143 143 0 0 1 224.7 302.1Z" fill="#e8226a"/>
    <path d="M170 170L224.7 302.1A143 143 0 0 1 115.3 302.1Z" fill="#5a22d6"/>
    <path d="M170 170L115.3 302.1A143 143 0 0 1 37.9 224.7Z" fill="#11a26a"/>
    <path d="M170 170L37.9 224.7A143 143 0 0 1 37.9 115.3Z" fill="#8e9096"/>
    <path d="M170 170L37.9 115.3A143 143 0 0 1 115.3 37.9Z" fill="#f04e1f"/>
    <g font-family="Inter,sans-serif" font-size="19" font-weight="700" fill="#fff" text-anchor="middle" dominant-baseline="middle">
      <text x="265" y="170" transform="rotate(-90 170 170)">100$</text>
      <text x="265" y="170" transform="rotate(-45 170 170)">200$</text>
      <text x="265" y="170">300$</text>
      <text x="265" y="170" transform="rotate(45 170 170)">400$</text>
      <text x="265" y="170" transform="rotate(90 170 170)">500$</text>
      <text x="265" y="170" transform="rotate(135 170 170)">600$</text>
      <text x="265" y="170" transform="rotate(180 170 170)">700$</text>
      <text x="265" y="170" transform="rotate(225 170 170)">800$</text>
    </g>
    <circle cx="170" cy="170" r="18" fill="#1c1d22" stroke="#6d6f77" stroke-width="2"/>
    <rect x="164" y="2" width="12" height="40" rx="6" fill="#f0a93a"/>
  </svg>
  <div class="btn" style="left:83px;top:700px;width:210px;height:44px;font-size:17px">Spin Now</div>
</section>

<!-- Reward popup -->
<section class="phone" style="left:945px">
  <div class="dim">
    <div class="status"><span>9:41</span>
      <svg width="76" height="14" viewBox="0 0 76 14"><rect x="0" y="9" width="3" height="4" fill="#fff"/><rect x="5" y="6" width="3" height="7" fill="#fff"/><rect x="10" y="3" width="3" height="10" fill="#fff"/><rect x="15" y="0" width="3" height="13" fill="#fff"/><path d="M28 5a10 10 0 0 1 14 0l-2 2a7 7 0 0 0-10 0zM31 8a5 5 0 0 1 8 0l-4 4z" fill="#fff"/><rect x="50" y="1" width="22" height="11" rx="3" fill="none" stroke="#fff"/><rect x="52" y="3" width="16" height="7" rx="1" fill="#fff"/></svg>
    </div>
    <svg class="abs" style="left:18px;top:62px" width="20" height="16" fill="none" stroke="#fff" stroke-width="1.6"><path d="M19 8H2M8 2L2 8l6 6"/></svg>
    <div class="abs" style="left:125px;top:125px;width:125px;height:40px;border-radius:8px;background:linear-gradient(90deg,#c41e1e,#f0a93a,#c41e1e)"></div>
    <h2 class="center-text spin-title" style="top:192px">Spin the Wheel</h2>
    <svg class="abs" style="left:17px;top:307px" width="340" height="340" viewBox="0 0 340 340"><circle cx="170" cy="170" r="166" fill="none" stroke="#8e6fd0" stroke-width="3"/><circle cx="170" cy="170" r="143" fill="#3a2a7a"/></svg>
    <div class="btn" style="left:83px;top:700px;width:210px;height:44px;font-size:17px">Spin Now</div>
  </div>
  <div class="modal" role="img" aria-label="Big win celebration with treasure chest and flying gold coins"></div>
  <p class="center-text" style="top:490px;font-size:17px;font-weight:700;color:var(--orange)">+60 freespins</p>
  <div class="close"><svg width="12" height="12"><path d="M1 1l10 10M11 1L1 11" stroke="#f0a93a" stroke-width="2.4"/></svg></div>
</section>

</body>
</html>
```